Small corporate website template design

I need a couple templates designed for a small corporate website. The corporate site reflects the existence of the parent company which will own various brands/services that have their own websites, so it will mainly be used to present who we are, what we do, what is happening (news/events), how to contact us, link off to our other brand/service sites, as well as post information for public relations, investors, and job opportunities.

The company name is Brelvanto LLC (www.brelvanto-example.com), and the name is representative of stratified layers of interconnected digital services. The corporate site is not expected to generate a bunch of fanfare - that honor will be reserved for the externally linked brand/service sites.

The provided logo may be manipulated in color, size, shape, positioning, etc. to get it to fit with the design, but should be integrated in some way.

What we are looking for is a home page layout as well as a template for an inner page whereby the navigation/logo, etc may be diminished to some extent for the inner pages. We are also interested in reusable elements such as dividers, content containers, etc. in order to represent the types of information described above that we would like to present as described above.

We are particularly interested in consistency of design elements, conservative use of color (including consideration of accessibility concerns), judicious use of whitespace in favor of simplified messaging, and something lending itself well to internationalization/translation.

Target Market(s)

Small business owners, entrepreneurs (B2B)

Number of Pages Required

2 page

Font styles to use
Sans Serif

Requirements
Must have
• See the attached PDF with the logo concept, color swatches, and comparative sites.

```html
<!DOCTYPE html>
<html lang="en">
<head>
<meta charset="utf-8">
<title>Brelvanto LLC</title>
<link href="https://fonts.googleapis.com/css2?family=Poppins:wght@400;500;600&family=Roboto:wght@400;500;700&family=Roboto+Condensed:wght@400;700&display=swap" rel="stylesheet">
<style>
:root{
  --navy:#050f24;
  --navy-2:#0a2a5e;
  --blue:#3d72c8;
  --blue-light:#5b8fe0;
  --orange:#f7931e;
  --ink:#1d1d1f;
  --text:#555a62;
  --white:#ffffff;
  --rule:#d9dde3;
}
*{box-sizing:border-box;margin:0;padding:0}
html,body{width:1200px;height:2965px;overflow:hidden}
body{position:relative;background:var(--white);font-family:"Poppins",sans-serif;color:var(--text)}

/* Hero */
.hero-shape{position:absolute;left:0;top:0;width:1200px;height:750px}
.brand{position:absolute;left:132px;top:58px;display:flex;align-items:center;gap:14px;color:var(--white);font-family:"Roboto Condensed",sans-serif;font-weight:700;font-size:34px;letter-spacing:.5px}
.brand-dot{width:22px;height:22px;border-radius:50%;background:var(--white)}
.main-nav{position:absolute;top:66px;left:468px;display:flex;gap:24px;font-family:"Roboto Condensed",sans-serif;font-size:17px;color:var(--white)}
.sign-in{position:absolute;left:978px;top:62px;width:89px;height:32px;border:2px solid var(--white);border-radius:16px;color:var(--white);font-family:"Poppins",sans-serif;font-weight:600;font-size:13px;display:flex;align-items:center;justify-content:center;letter-spacing:.5px}
.hero-title{position:absolute;top:262px;left:0;width:1200px;text-align:center;color:var(--white);font-family:"Roboto",sans-serif;font-weight:500;font-size:40px;line-height:54px;letter-spacing:.5px}
.hero-btn{position:absolute;left:506px;top:393px;width:188px;height:38px;border:2px solid var(--white);border-radius:19px;color:var(--white);font-weight:500;font-size:14px;display:flex;align-items:center;justify-content:center}
.slider-dots{position:absolute;top:470px;left:563px;display:flex;gap:10px;align-items:center}
.slider-dots span{width:11px;height:11px;border-radius:50%;background:var(--white)}
.slider-dots .active{width:17px;height:17px;background:transparent;border:2px solid var(--white);position:relative}
.slider-dots .active::after{content:"";position:absolute;left:3px;top:3px;width:7px;height:7px;border-radius:50%;background:var(--white)}

/* Services */
.section-title{position:absolute;left:0;width:1200px;text-align:center;font-family:"Roboto",sans-serif;font-size:40px;font-weight:700;color:var(--ink)}
.section-title .light{color:var(--blue);font-weight:400}
.service-card{position:absolute;top:937px;width:299px;height:382px;background:var(--white);box-shadow:0 2px 10px rgba(0,0,0,.18);text-align:center}
.service-icon{position:absolute;left:84px;top:34px;width:130px;height:130px}
.service-card h3{position:absolute;top:188px;left:0;width:100%;font-weight:500;font-size:16px;color:var(--ink)}
.service-card p{position:absolute;top:222px;left:16px;width:267px;font-size:12px;line-height:25px;color:var(--text)}
.card-btn{position:absolute;left:93px;top:313px;width:112px;height:31px;border:2px solid #c9cdd3;border-radius:16px;font-size:12.5px;color:var(--ink);display:flex;align-items:center;justify-content:center}

/* What we do */
.what-band{position:absolute;left:0;top:1430px;width:1200px;height:530px}
.what-title{position:absolute;top:1572px;left:0;width:1200px;text-align:center;color:var(--white);font-weight:600;font-size:40px;letter-spacing:.5px}
.what-copy{position:absolute;top:1644px;left:180px;width:840px;text-align:center;color:var(--white);font-size:13px;line-height:26px}
.what-btn{position:absolute;left:534px;top:1781px;width:132px;height:36px;border:2px solid var(--white);border-radius:18px;color:var(--white);font-weight:500;font-size:13px;display:flex;align-items:center;justify-content:center}

/* Investors */
.laptop-art{position:absolute;left:119px;top:2026px;width:346px;height:346px;border-radius:8px;background:linear-gradient(150deg,#3a55b8 0%,#8fa3d9 55%,#e6ebf5 100%)}
.investors-rule{position:absolute;left:504px;top:2076px;width:1px;height:257px;background:var(--rule)}
.investors-title{position:absolute;left:569px;top:2074px;font-family:"Roboto",sans-serif;font-weight:500;font-size:32px;color:var(--ink)}
.investors-copy{position:absolute;left:569px;top:2137px;width:520px;font-size:12px;line-height:25px;color:var(--text)}
.orange-btn{position:absolute;left:569px;top:2296px;width:119px;height:32px;border-radius:16px;background:var(--orange);color:var(--white);font-size:13px;display:flex;align-items:center;justify-content:center;box-shadow:0 2px 4px rgba(0,0,0,.2)}

/* Footer */
.footer-shape{position:absolute;left:0;top:2400px;width:1200px;height:565px}
.footer-heading{position:absolute;top:2585px;color:var(--white);font-family:"Roboto",sans-serif;font-weight:700;font-size:20px;letter-spacing:.3px}
.contact-item{position:absolute;left:132px;display:flex;gap:14px;color:var(--white);font-size:12.5px;line-height:18px}
.contact-item svg{flex:none;margin-top:1px}
.signup-copy{position:absolute;left:393px;top:2636px;width:300px;color:var(--white);font-size:11px;line-height:18px}
.email-field{position:absolute;left:393px;top:2696px;width:309px;height:32px;border-radius:16px;background:var(--white);overflow:hidden;display:flex}
.email-field .placeholder{flex:1;padding-left:16px;font-size:11px;color:#777;display:flex;align-items:center}
.email-field .subscribe{width:103px;background:var(--orange);color:var(--white);font-weight:600;font-size:12px;display:flex;align-items:center;justify-content:center;border-radius:16px}
.quick-links{position:absolute;left:797px;top:2634px;list-style:none;color:var(--white);font-size:12px;line-height:22.5px}
.footer-brand{position:absolute;left:930px;top:2652px;width:170px;display:flex;align-items:center;gap:10px;color:var(--white);font-family:"Roboto Condensed",sans-serif;font-weight:700;font-size:28px}
.footer-brand .brand-dot{width:18px;height:18px}
.footer-rule{position:absolute;left:0;top:2817px;width:1200px;height:1px;background:rgba(255,255,255,.12)}
.social{position:absolute;top:2862px;left:543px;display:flex;gap:6px}
.social span{width:26px;height:26px;border-radius:50%;border:1.5px solid var(--white)}
.copyright{position:absolute;top:2912px;left:0;width:1200px;text-align:center;color:var(--white);font-size:12.5px}
</style>
</head>
<body>

<header class="hero">
  <svg class="hero-shape" viewBox="0 0 1200 750" role="img" aria-label="Dark blue network backdrop with glowing connection nodes and security icons">
    <defs>
      <linearGradient id="heroFill" x1="0" y1="0" x2="0" y2="1">
        <stop offset="0" stop-color="#02060f"/>
        <stop offset=".45" stop-color="#071a3d"/>
        <stop offset="1" stop-color="#0d3a7a"/>
      </linearGradient>
    </defs>
    <path d="M0 0H1200V470Q1200 515 1160 530L600 738L40 530Q0 515 0 470Z" fill="url(#heroFill)"/>
    <path d="M1200 470Q1200 515 1160 530L600 738L40 530Q0 515 0 470" fill="none" stroke="#f7931e" stroke-width="5"/>
  </svg>

  <div class="brand"><span class="brand-dot"></span>Brelvanto</div>
  <nav class="main-nav">
    <span>HOME</span><span>WHO WE ARE</span><span>SERVICE</span><span>INVESTORS</span><span>NEWS</span><span>CONTACT</span>
  </nav>
  <div class="sign-in">SIGN IN</div>

  <h1 class="hero-title">ADAPTIVE SOFTWARE TECHNOLOGY<br>FOR THE DIGITAL REVOLUTION</h1>
  <div class="hero-btn">JOB OPPORTUNITIES</div>
  <div class="slider-dots"><span class="active"></span><span></span><span></span><span></span></div>
</header>

<section class="services">
  <h2 class="section-title" style="top:832px"><span class="light">OUR</span> SERVICES</h2>

  <article class="service-card" style="left:128px">
    <svg class="service-icon" viewBox="0 0 130 130">
      <circle cx="8" cy="32" r="6" fill="#3d72c8"/><circle cx="126" cy="88" r="3" fill="#3d72c8"/>
      <polygon points="65,4 117,34 117,94 65,124 13,94 13,34" fill="none" stroke="#3d72c8" stroke-width="2"/>
      <polygon points="65,12 110,38 110,90 65,116 20,90 20,38" fill="#3d72c8"/>
      <path d="M44 80H88M46 74L58 60L68 68L84 50M78 50H84V56" fill="none" stroke="#fff" stroke-width="4" stroke-linecap="round" stroke-linejoin="round"/>
    </svg>
    <h3>QUIS AUTEM VEL EUM</h3>
    <p>Sed ut perspiciatis unde omnis iste<br>natus error sit voluptatem accusantium<br>doloremque laudantium, totam</p>
    <div class="card-btn">Read More</div>
  </article>

  <article class="service-card" style="left:449px">
    <svg class="service-icon" viewBox="0 0 130 130">
      <circle cx="8" cy="32" r="6" fill="#3d72c8"/><circle cx="126" cy="88" r="3" fill="#3d72c8"/>
      <polygon points="65,4 117,34 117,94 65,124 13,94 13,34" fill="none" stroke="#3d72c8" stroke-width="2"/>
      <polygon points="65,12 110,38 110,90 65,116 20,90 20,38" fill="#3d72c8"/>
      <path d="M52 60V50a13 13 0 0 1 25-4" fill="none" stroke="#fff" stroke-width="5" stroke-linecap="round"/>
      <rect x="47" y="60" width="36" height="28" rx="3" fill="#fff"/>
      <rect x="63" y="68" width="4" height="11" rx="2" fill="#3d72c8"/>
    </svg>
    <h3>QUIS AUTEM VEL EUM</h3>
    <p>Sed ut perspiciatis unde omnis iste<br>natus error sit voluptatem accusantium<br>doloremque laudantium, totam</p>
    <div class="card-btn">Read More</div>
  </article>

  <article class="service-card" style="left:767px">
    <svg class="service-icon" viewBox="0 0 130 130">
      <circle cx="8" cy="32" r="6" fill="#3d72c8"/><circle cx="126" cy="88" r="3" fill="#3d72c8"/>
      <polygon points="65,4 117,34 117,94 65,124 13,94 13,34" fill="none" stroke="#3d72c8" stroke-width="2"/>
      <polygon points="65,12 110,38 110,90 65,116 20,90 20,38" fill="#3d72c8"/>
      <path d="M65 42a16 16 0 0 0-9 29v7h18v-7a16 16 0 0 0-9-29z" fill="#fff"/>
      <rect x="57" y="81" width="16" height="4" rx="2" fill="#fff"/>
      <rect x="59" y="87" width="12" height="4" rx="2" fill="#fff"/>
    </svg>
    <h3>QUIS AUTEM VEL EUM</h3>
    <p>Sed ut perspiciatis unde omnis iste<br>natus error sit voluptatem accusantium<br>doloremque laudantium, totam</p>
    <div class="card-btn">Read More</div>
  </article>
</section>

<section class="what-we-do">
  <svg class="what-band" viewBox="0 0 1200 530" role="img" aria-label="Deep blue digital network mesh backdrop">
    <defs>
      <linearGradient id="bandFill" x1="0" y1="0" x2="1" y2="1">
        <stop offset="0" stop-color="#0a2a6e"/>
        <stop offset=".5" stop-color="#0b3a8e"/>
        <stop offset="1" stop-color="#06214f"/>
      </linearGradient>
    </defs>
    <polygon points="0,0 1200,52 1200,524 0,484" fill="url(#bandFill)"/>
  </svg>
  <h2 class="what-title">WHAT WE DO</h2>
  <p class="what-copy">We are a team of U.S.-based systems developers &amp; administrators, technical consultants, and operational subject matter experts that deliver highly customized, boutique, and/or enterprise level solutions to large government organizations and international businesses. Our team has delivered highly technical cyber defense and communication solutions in over 50 countries in both remote and austere environments as well as highly developed nations.</p>
  <div class="what-btn">READ MORE</div>
</section>

<section class="investors">
  <div class="laptop-art" role="img" aria-label="Isometric illustration of a laptop showing charts and graphs"></div>
  <div class="investors-rule"></div>
  <h2 class="investors-title">BRELVANTO INVESTORS</h2>
  <p class="investors-copy">Sed ut perspiciatis unde omnis iste natus error sit voluptatem accusantium doloremque laudantium, totam rem aperiam, eaque ipsa quae ab illo inventore veis et quasi architecto beatae vitae dicta sunt explicabo. Nemo enim ipsam vuptatem quia voluptas sit aspernatur aut odit aut fugit, sed quia consequuntur magni lores eos qui ratione voluptatem sequi nesciunt. Neque porro quisquam est</p>
  <div class="orange-btn">Read More</div>
</section>

<footer class="site-footer">
  <svg class="footer-shape" viewBox="0 0 1200 565">
    <polygon points="1010,40 1200,10 1200,70" fill="#3d72c8"/>
    <polygon points="0,100 180,128 0,158" fill="#3d72c8"/>
    <polygon points="0,128 1200,30 1200,565 0,565" fill="#050f24"/>
  </svg>

  <h3 class="footer-heading" style="left:132px">CONTACT US</h3>
  <div class="contact-item" style="top:2640px">
    <svg width="16" height="20" viewBox="0 0 16 20"><path d="M8 1a6 6 0 0 0-6 6c0 5 6 12 6 12s6-7 6-12a6 6 0 0 0-6-6z" fill="none" stroke="#fff" stroke-width="1.5"/><circle cx="8" cy="7" r="2" fill="#fff"/></svg>
    <span>Brelvanto<br>&nbsp;Lindor St, Halvern 4071<br>Victoria, Australia</span>
  </div>
  <div class="contact-item" style="top:2704px">
    <svg width="16" height="16" viewBox="0 0 16 16"><path d="M3 1l3 3-2 2c1 2 3 4 5 5l2-2 3 3-2 3C7 15 1 9 1 3z" fill="none" stroke="#fff" stroke-width="1.3" stroke-linejoin="round"/></svg>
    <span>Phone : 1300 555 014</span>
  </div>
  <div class="contact-item" style="top:2736px">
    <svg width="16" height="14" viewBox="0 0 16 14"><rect x="1" y="2" width="14" height="10" fill="none" stroke="#fff" stroke-width="1.3"/><path d="M1 2l7 6 7-6" fill="none" stroke="#fff" stroke-width="1.3"/></svg>
    <span>info@brelvanto-example.com</span>
  </div>

  <h3 class="footer-heading" style="left:393px">SIGN UP TO RECEIVE EMAIL</h3>
  <p class="signup-copy">Excepteur sint occaecat cupidatat non proident, sunt in culpa qui Nemo enim ipsam voluptatem</p>
  <div class="email-field"><span class="placeholder">Enter Email</span><span class="subscribe">SUBSCRIBE</span></div>

  <h3 class="footer-heading" style="left:797px">QUICK LINKS</h3>
  <ul class="quick-links">
    <li>Home</li><li>Who We Are</li><li>Service</li><li>Investors</li><li>News</li><li>Contact</li>
  </ul>

  <div class="footer-brand"><span class="brand-dot"></span>Brelvanto</div>

  <div class="footer-rule"></div>
  <div class="social"><span></span><span></span><span></span><span></span></div>
  <p class="copyright">Copyright © Brelvanto 2018. All rights reserved.</p>
</footer>

</body>
</html>
```